1876 Basins & Spouts Business Card

I'm wanting to get a business card designed. Our business is 1876 Basins & Spouts
Details for the card:

1876 Basins & Spouts
Name: Harold Vesk
Email: harold@1876basinsandspouts.com.au
Website: www.1876basinsandspouts.com.au
Mobile: 0438 260 947
Phone: 02 7481 3926

Font of Basins & Spouts is called Snell Roundhand. Not sue what font logo text is.

I'm thinking two sided but it doesn't have to be.

```html
<!DOCTYPE html>
<html lang="en">
<head>
<meta charset="utf-8">
<title>1876 Basins &amp; Spouts — Business Card</title>
<link rel="stylesheet" href="https://fonts.googleapis.com/css2?family=Lato:wght@400;700&display=swap">
<style>
  :root {
    --backdrop: #5f5f5f;
    --card-light: #ffffff;
    --card-dark: #0b0b0d;
    --ink: #111111;
    --ink-soft: #555555;
    --ink-inverse: #ffffff;
    --rule: #333333;
  }
  * { margin: 0; padding: 0; box-sizing: border-box; }
  html, body {
    width: 1200px; height: 1200px; overflow: hidden;
    background: var(--backdrop);
    font-family: "Lato", Arial, sans-serif;
  }
  .canvas { position: relative; width: 1200px; height: 1200px; }
  .card {
    position: absolute; left: 240px; width: 720px; height: 420px;
    border-radius: 36px;
  }
  .card--front { top: 142px; background: var(--card-light); }
  .card--back { top: 638px; background: var(--card-dark); }

  .brand {
    position: absolute; left: 0; right: 0;
    text-align: center;
  }
  .brand__name {
    font-size: 34px; font-weight: 400; letter-spacing: 0.5px;
  }
  .brand__tagline {
    margin-top: 8px; font-size: 12px; font-weight: 400;
  }
  .card--front .brand { top: 98px; color: var(--ink); }
  .card--back .brand { top: 190px; color: var(--ink-inverse); }
  .card--back .brand__tagline { font-size: 13px; }

  .holder {
    position: absolute; right: 382px; top: 261px;
    font-size: 25px; line-height: 30px; font-weight: 700; color: var(--ink);
    white-space: nowrap;
  }
  .divider {
    position: absolute; left: 360px; top: 230px;
    width: 2px; height: 94px; background: var(--rule);
  }
  .contacts {
    position: absolute; left: 382px; top: 225px;
    list-style: none;
  }
  .contacts li {
    display: flex; align-items: center; gap: 10px;
    height: 26px; font-size: 18px; color: var(--ink-soft);
  }
  .contacts svg { width: 13px; height: 13px; fill: var(--ink); flex: none; }

  .back-footer {
    position: absolute; left: 0; right: 0; top: 360px;
    text-align: center; font-size: 18px; color: var(--ink-inverse);
  }
</style>
</head>
<body>
<main class="canvas">
  <section class="card card--front" aria-label="Card front">
    <div class="brand">
      <div class="brand__name">1876 Basins &amp; Spouts</div>
      <div class="brand__tagline">Pairing classic elegance with everyday reliability</div>
    </div>
    <div class="holder">Harold Vesk</div>
    <div class="divider"></div>
    <ul class="contacts">
      <li>
        <svg viewBox="0 0 16 16" aria-hidden="true"><path d="M3.5 1l3 3-1.8 1.8c.9 2 2.5 3.6 4.5 4.5L11 8.5l3 3-2 2.5C6.5 14 2 9.5 1 3z"/></svg>
        02 7481 3926
      </li>
      <li>
        <svg viewBox="0 0 16 16" aria-hidden="true"><path d="M4 0h8a1 1 0 0 1 1 1v14a1 1 0 0 1-1 1H4a1 1 0 0 1-1-1V1a1 1 0 0 1 1-1zm1 2v10h6V2zm3 11a1 1 0 1 0 0 2 1 1 0 0 0 0-2z"/></svg>
        0438 260 947
      </li>
      <li>
        <svg viewBox="0 0 16 16" aria-hidden="true"><path d="M1 3h14v10H1zm1.5 1.2L8 8.5l5.5-4.3z"/></svg>
        harold@1876basinsandspouts.com.au
      </li>
      <li>
        <svg viewBox="0 0 16 16" aria-hidden="true"><path d="M8 0a8 8 0 1 0 0 16A8 8 0 0 0 8 0zm0 1.5c.9 0 2 1.9 2.3 4.5H5.7C6 3.4 7.1 1.5 8 1.5zM1.6 7h2.9c0 .7 0 1.4.1 2H1.6a6.5 6.5 0 0 1 0-2zm4.1 3h4.6C10 12.6 8.9 14.5 8 14.5S6 12.6 5.7 10zm5.8-3h2.9a6.5 6.5 0 0 1 0 2h-2.9c.1-.6.1-1.3 0-2z"/></svg>
        www.1876basinsandspouts.com.au
      </li>
    </ul>
  </section>

  <section class="card card--back" aria-label="Card back">
    <div class="brand">
      <div class="brand__name">1876 Basins &amp; Spouts</div>
      <div class="brand__tagline">Pairing classic elegance with everyday reliability</div>
    </div>
    <div class="back-footer">1876 Basins &amp; Spouts</div>
  </section>
</main>
</body>
</html>
```